Im open to ideas.. I was thinking on my business cards aswell as my logo. a place for my name. email. phone number and abn..

ive attched a file with my business logo. which i dont love the colours.. i was think a dark background with charcoal letters so something along those colour schumes but im open to ideas..

BRM Constructions

```html
<!DOCTYPE html>
<html lang="en">
<head>
<meta charset="utf-8">
<title>BRM Constructions – Business Cards</title>
<link href="https://fonts.googleapis.com/css2?family=Open+Sans:wght@400;600;700;800&display=swap" rel="stylesheet">
<style>
  :root {
    --backdrop: #e6e6e6;
    --card-front: #0d0d0d;
    --card-back: #4d4d4d;
    --brand-grey: #9b9b9b;
    --text-light: #ffffff;
    --text-soft: #d9d9d9;
    --divider: #3a3a3a;
  }
  * { margin: 0; padding: 0; box-sizing: border-box; }
  html, body {
    width: 1200px; height: 900px; overflow: hidden;
    background: var(--backdrop);
    font-family: "Open Sans", Arial, sans-serif;
  }
  .card {
    position: absolute; top: 306px;
    width: 440px; height: 271px;
    border-radius: 10px;
  }
  .card--front { left: 149px; background: var(--card-front); }
  .card--back  { left: 608px; background: var(--card-back); }

  .brand-name {
    position: absolute; left: 0; right: 0;
    text-align: center; font-weight: 800; line-height: 1;
  }
  .brand-name__main { display: block; font-size: 46px; letter-spacing: 2px; }
  .brand-name__sub  { display: block; font-size: 11px; letter-spacing: 6px; margin-top: 6px; padding-left: 6px; }
  .card--front .brand-name { top: 88px; color: var(--brand-grey); }
  .card--back  .brand-name { top: 138px; color: var(--text-light); }

  .abn {
    position: absolute; top: 158px; left: 0; right: 0;
    text-align: center; font-size: 11px; color: var(--text-light);
  }
  .abn strong { font-weight: 700; }

  .holder {
    position: absolute; right: 235px; top: 199px;
    text-align: right; color: var(--text-light);
  }
  .holder__name { font-size: 14px; font-weight: 600; line-height: 18px; }
  .holder__role { font-size: 12px; color: var(--text-soft); line-height: 16px; }

  .contact-divider {
    position: absolute; left: 221px; top: 190px;
    width: 1px; height: 44px; background: var(--divider);
  }
  .contact-list {
    position: absolute; left: 234px; top: 190px;
    list-style: none; color: var(--text-light);
    font-size: 11.5px; line-height: 15.5px;
  }
  .contact-list li { display: flex; align-items: center; gap: 6px; }
  .contact-list svg { width: 10px; height: 10px; fill: var(--text-light); flex: none; }
</style>
</head>
<body>
  <section class="card card--front" aria-label="Business card front">
    <div class="brand-name">
      <span class="brand-name__main">BRM</span>
      <span class="brand-name__sub">CONSTRUCTIONS</span>
    </div>
    <p class="abn"><strong>ABN:</strong>7654321</p>
    <div class="holder">
      <p class="holder__name">Daniel Reeves</p>
      <p class="holder__role">Managing Director</p>
    </div>
    <div class="contact-divider"></div>
    <ul class="contact-list">
      <li>
        <svg viewBox="0 0 10 10" aria-hidden="true"><path d="M1 3.5 Q5 0.5 9 3.5 L8 5 L6.5 4 L6.5 3 Q5 2.5 3.5 3 L3.5 4 L2 5 Z M2.5 5.5 H7.5 L8.5 9 H1.5 Z"/></svg>
        044-987 654 321
      </li>
      <li>
        <svg viewBox="0 0 10 10" aria-hidden="true"><path d="M1 2.5 H9 V8 H1 Z" /><path d="M1 2.5 L5 5.5 L9 2.5" stroke="#0d0d0d" stroke-width="0.9" fill="none"/></svg>
        info@brmbuild.com
      </li>
      <li>
        <svg viewBox="0 0 10 10" aria-hidden="true"><circle cx="5" cy="5" r="4.3"/><path d="M3 3.5 Q4.5 2.5 5.5 4 Q4.5 5 5.5 6.5 L4.5 8 Q3.5 6 3 5 Z M6.5 2.5 Q8 3.5 7.5 5 Q6.5 4.5 6.5 2.5 Z" fill="#0d0d0d"/></svg>
        www.brmbuild.com
      </li>
    </ul>
  </section>

  <section class="card card--back" aria-label="Business card back">
    <div class="brand-name">
      <span class="brand-name__main">BRM</span>
      <span class="brand-name__sub">CONSTRUCTIONS</span>
    </div>
  </section>
</body>
</html>
```